Corporate Brochure Cover Design

We need a design for a corporate A4 Size portfolio cover (front and back) which we will be distributing. to our commercial clients.

We are a professional plumbing company that is an industry leader for service we provide to our clients and technology we use. The design needs to incorporate the colours black, red, white and silver and needs to include our logo. We dont have any slogans or mottos... If you wanted to use something it could be "Delivering exceptional service...Always!" however i dont want it to b the focal point of the cover.

Im looking for something professional and modern that has the WOW factor!

Size is A4 - both front and back covers. You can include pictures as well or sample pictures of where we can source and put our own team pictures.

if you have any questions, please do not hesitate to contact me.

Target Market(s)

Our commercial & strata clients - professional industry.

Industry/Entity Type

Commercial

Font styles to use
Sans Serif

Requirements
Must have
• Red, black, white, silver as the colour scheme.
• Include the logo.
Nice to have
• Modern design and something that makes the client go WOW before they open the brochure.
Should not have
• lots of text

```html
<!DOCTYPE html>
<html lang="en">
<head>
<meta charset="utf-8">
<title>Northline Portfolio Cover</title>
<link rel="stylesheet" href="https://fonts.googleapis.com/css2?family=Roboto:wght@400;500;700&display=swap">
<style>
  :root {
    --page: #ffffff;
    --cover: #121212;
    --red: #c8102e;
    --red-deep: #8e0b21;
    --white: #ffffff;
    --silver: #b5b5b5;
    --label: #222222;
  }
  html, body {
    margin: 0;
    width: 1200px;
    height: 874px;
    overflow: hidden;
    background: var(--page);
    font-family: "Roboto", Arial, sans-serif;
  }
  .canvas { position: relative; width: 1200px; height: 874px; }
  .cover {
    position: absolute;
    top: 24px;
    width: 548px;
    height: 750px;
    background: var(--cover);
    overflow: hidden;
  }
  .cover--back { left: 37px; }
  .cover--front { left: 598px; }
  .side-label {
    position: absolute;
    top: 799px;
    width: 548px;
    text-align: center;
    font-size: 13px;
    color: var(--label);
  }
  .side-label--back { left: 37px; }
  .side-label--front { left: 598px; }

  .brand {
    position: absolute;
    left: 0;
    width: 100%;
    display: flex;
    justify-content: center;
    align-items: center;
    color: var(--white);
    font-weight: 700;
    letter-spacing: 1px;
  }
  .brand-dot { border-radius: 50%; background: var(--red); }
  .brand--front { top: 100px; font-size: 42px; gap: 12px; }
  .brand--front .brand-dot { width: 16px; height: 16px; }
  .brand--back { top: 465px; font-size: 27px; gap: 8px; }
  .brand--back .brand-dot { width: 11px; height: 11px; }

  .back-info {
    position: absolute;
    left: 0;
    width: 100%;
    text-align: center;
  }
  .office-title { top: 556px; font-size: 13.5px; letter-spacing: 1.5px; color: var(--silver); }
  .office-address { top: 583px; font-size: 10px; line-height: 15px; color: var(--silver); }
  .support-title { top: 635px; font-size: 12px; letter-spacing: 1px; color: var(--red); }
  .support-phones { top: 653px; font-size: 12.5px; color: var(--white); }
  .web-contact { top: 704px; font-size: 10px; color: var(--silver); }

  .brush-area {
    position: absolute;
    left: 0;
    top: 416px;
    width: 548px;
    height: 260px;
    background: linear-gradient(110deg, var(--red-deep) 0%, var(--red) 45%, var(--red) 70%, var(--silver) 100%);
  }
  .front-tagline {
    position: absolute;
    left: 0;
    top: 690px;
    width: 100%;
    text-align: center;
    font-size: 16.5px;
    font-weight: 500;
    color: var(--white);
  }
</style>
</head>
<body>
<main class="canvas">
  <section class="cover cover--back">
    <div class="brand brand--back"><span class="brand-dot"></span>NORTHLINE</div>
    <div class="back-info office-title">CORPORATE OFFICE</div>
    <div class="back-info office-address">#48, HARBOUR VIEW PARADE, EASTWOOD.<br>NEW SOUTH. AUSTRALIA. 204518</div>
    <div class="back-info support-title">SUPPORT</div>
    <div class="back-info support-phones">1800 555 0142, 1800 555 0198</div>
    <div class="back-info web-contact">Email: help@northlineplumbing.com &nbsp;|&nbsp; Web: www.northlineplumbing.com</div>
  </section>

  <section class="cover cover--front">
    <div class="brand brand--front"><span class="brand-dot"></span>NORTHLINE</div>
    <div class="brush-area" role="img" aria-label="Decorative red and white brush-stroke swoosh arcing across the lower cover"></div>
    <div class="front-tagline">DELIVERING EXCEPTIONAL SERVICE... ALWAYS!</div>
  </section>

  <div class="side-label side-label--back">Back</div>
  <div class="side-label side-label--front">Front</div>
</main>
</body>
</html>
```